DJ Colm Vetter

I'm looking for a professional but still artsy/progressive design. I come from a hip hop/club DJ background playing a lot of underground music but have switched to doing more corporate parties and weddings recently. I am all about keeping the dancefloor moving and emotionally connecting with the crowd. I'd like a trendy/updated color palette. Something that's clean enough that looks professional but also trendy enough to convey that by the end of the night we'll be sweatily dancing to the latest hits. Some designers/artists I like: Tarn Olquist, Pavel Remy, Wendell Quarrie, Lumeno 7400, Silas Dravin.

```html
<!DOCTYPE html>
<html lang="en">
<head>
<meta charset="utf-8">
<title>DJ Colm Vetter — Business Card</title>
<link rel="stylesheet" href="https://fonts.googleapis.com/css2?family=Saira+Condensed:wght@300&display=swap">
<style>
  :root {
    --backdrop: #d9d9d9;
    --card: #1c1c1c;
    --card-edge: #141414;
    --ink-bright: #e8e8e8;
    --ink-dim: #6f6f6f;
    --mark-silver: #cfcfcf;
  }
  html, body {
    margin: 0;
    padding: 0;
    width: 1200px;
    height: 796px;
    overflow: hidden;
    background: var(--backdrop);
  }
  .canvas {
    position: relative;
    width: 1200px;
    height: 796px;
    display: flex;
    align-items: center;
    justify-content: center;
  }
  .card {
    position: relative;
    width: 840px;
    height: 480px;
    background: var(--card);
    border: 1px solid var(--card-edge);
    box-shadow: 0 18px 40px rgba(0, 0, 0, 0.25);
    font-family: "Saira Condensed", "Arial Narrow", sans-serif;
  }
  .brand {
    position: absolute;
    left: 84px;
    top: 50%;
    transform: translateY(-50%);
    display: flex;
    align-items: center;
    gap: 12px;
  }
  .brand-square {
    width: 12px;
    height: 12px;
    background: var(--mark-silver);
  }
  .brand-name {
    color: var(--mark-silver);
    font-weight: 300;
    font-size: 15px;
    letter-spacing: 0.3em;
    text-transform: uppercase;
    white-space: nowrap;
    line-height: 1;
  }
  .dj-name {
    position: absolute;
    left: 300px;
    top: 50%;
    transform: translateY(-50%);
    margin: 0;
    font-weight: 300;
    font-size: 22px;
    line-height: 1;
    letter-spacing: 0.95em;
    text-transform: uppercase;
    white-space: nowrap;
    color: var(--ink-bright);
  }
  .dj-name .prefix {
    color: var(--ink-dim);
    margin-right: 1.6em;
  }
</style>
</head>
<body>
  <main class="canvas">
    <section class="card" aria-label="DJ Colm Vetter business card">
      <div class="brand">
        <span class="brand-square"></span>
        <span class="brand-name">Vetter Sound</span>
      </div>
      <h1 class="dj-name"><span class="prefix">DJ</span>Colm Vetter</h1>
    </section>
  </main>
</body>
</html>
```